Quorva - corporate Business Card

We need a good look and innovative business card for a new start up company based in Los Angeles called "Quorva". We are in a payment business, including payment card, app, and ewallet. We are expert in online payment and Card not present (CNP) transaction.
We need an innovative, modern business card.

Our logo font is Aero Matics

Target Market(s)

Startup - Bank - Online Payment - Card Manufacturing

Industry/Entity Type

Startup

Contact Information for Business Card

phone: 555 014 7396 - Address: 4172 Marlowe blvd, Fenridge, NV 89014

Requirements
Must have
• Message: innovative, professional, expert, high tech, trust, online payment expert, security
Nice to have
• no comment
Should not have
• no Comment

```html
<!DOCTYPE html>
<html lang="en">
<head>
<meta charset="utf-8">
<title>Quorva – Business Card</title>
<link rel="stylesheet" href="https://fonts.googleapis.com/css2?family=Lato:wght@400;700;900&display=swap">
<style>
  :root {
    --brand-red: #b31d2b;
    --brand-red-soft: rgba(255, 255, 255, 0.2);
    --ink-black: #0d0d0d;
    --paper: #ffffff;
    --stage: #ececec;
    --text-light: #ffffff;
  }
  * { margin: 0; padding: 0; box-sizing: border-box; }
  html, body {
    width: 1200px; height: 586px; overflow: hidden;
    background: var(--stage);
    font-family: "Lato", Arial, sans-serif;
  }
  .canvas { position: relative; width: 1200px; height: 586px; }
  .card {
    position: absolute; top: 129px;
    width: 501px; height: 300px; overflow: hidden;
  }
  .card-front { left: 61px; background: var(--brand-red); }
  .card-back { left: 619px; background: var(--paper); }

  .front-disc {
    position: absolute; left: 276px; top: 22px;
    width: 262px; height: 262px; border-radius: 50%;
    background: var(--brand-red-soft);
  }
  .front-name {
    position: absolute; left: 29px; top: 215px;
    font-size: 42px; font-weight: 700; color: var(--text-light);
    line-height: 1; letter-spacing: 0.5px;
  }
  .front-web {
    position: absolute; left: 32px; top: 262px;
    font-size: 11px; font-weight: 700; color: var(--text-light);
    letter-spacing: 3px;
  }

  .back-shape { position: absolute; inset: 0; }
  .back-brand {
    position: absolute; left: 143px; top: 35px;
    display: flex; align-items: center; gap: 8px;
  }
  .brand-dot {
    width: 60px; height: 60px; border-radius: 50%;
    background: var(--brand-red);
  }
  .brand-name {
    font-size: 40px; font-weight: 700; color: var(--brand-red);
    line-height: 1;
  }
  .identity {
    position: absolute; right: 291px; top: 188px;
    text-align: right; color: var(--text-light);
  }
  .person-name { font-size: 17px; font-weight: 900; }
  .person-role { font-size: 11px; margin-top: 5px; }
  .address { font-size: 12px; font-weight: 700; margin-top: 14px; line-height: 17px; }
  .divider {
    position: absolute; left: 236px; top: 178px;
    width: 1px; height: 110px;
    background: linear-gradient(transparent, rgba(255,255,255,0.7), transparent);
  }
  .contacts {
    position: absolute; left: 258px; top: 190px;
    list-style: none; color: var(--text-light); font-size: 12.5px;
  }
  .contacts li { display: flex; align-items: center; gap: 8px; height: 28px; }
  .contacts svg { width: 16px; height: 16px; flex: none; }
</style>
</head>
<body>
<main class="canvas">
  <section class="card card-front" aria-label="Card front">
    <div class="front-disc"></div>
    <div class="front-name">quorva</div>
    <div class="front-web">www.quorvawebsite.com</div>
  </section>

  <section class="card card-back" aria-label="Card back">
    <svg class="back-shape" viewBox="0 0 501 300" preserveAspectRatio="none">
      <path d="M0,163 Q250,95 501,163 L501,300 L0,300 Z" fill="var(--ink-black)"/>
      <path d="M0,190 Q250,80 501,200 L501,300 L0,300 Z" fill="var(--brand-red)"/>
    </svg>
    <div class="back-brand">
      <span class="brand-dot"></span>
      <span class="brand-name">quorva</span>
    </div>
    <div class="identity">
      <div class="person-name">Marcus Hale</div>
      <div class="person-role">Owner &amp; Founder</div>
      <div class="address">4172 Marlowe blvd,<br>Fenridge, NV 89014</div>
    </div>
    <div class="divider"></div>
    <ul class="contacts">
      <li>
        <svg viewBox="0 0 16 16"><circle cx="8" cy="8" r="8" fill="#fff"/><path d="M4 9.5c0-3 8-3 8 0v1H10V9.5H6v1H4z M6.5 8.5h3l1 3h-5z" fill="var(--brand-red)"/></svg>
        (555) 014-7396
      </li>
      <li>
        <svg viewBox="0 0 16 16"><circle cx="8" cy="8" r="8" fill="#fff"/><rect x="5.5" y="4" width="5" height="3" fill="var(--brand-red)"/><rect x="4" y="7" width="8" height="3.5" fill="var(--brand-red)"/><rect x="5.5" y="10" width="5" height="2" fill="var(--brand-red)"/></svg>
        (555) 014-7300
      </li>
      <li>
        <svg viewBox="0 0 16 16"><circle cx="8" cy="8" r="8" fill="#fff"/><rect x="4" y="5" width="8" height="6" fill="var(--brand-red)"/><path d="M4 5l4 3.5L12 5" stroke="#fff" stroke-width="0.9" fill="none"/></svg>
        MarcusH@quorvaweb.com
      </li>
    </ul>
  </section>
</main>
</body>
</html>
```